Rultan Staffing Full Length Retractable Office Banner

I need a design for a full-length retractable banner and A-Frame Sign for each of my offices. I have included designs that have been incorporated into a poster and tri-fold as a sample. I would like to see a colorful eyecatching banner that focuses on people. Would like to see some diversity with men and woman and different races.
Rultan Staffing is a light industrial staffing firm. www.RultanStaffing.example

Target Market(s)

Job seekers looking for employment

Industry/Entity Type

Staffing / Recruiting

Font styles to use
Other font styles liked:
• Professional yet fun

Requirements
Must have
• Eye catching design with young hip vibe.
Nice to have
• primary colors with light industrial type jobs

```html
<!DOCTYPE html>
<html lang="en">
<head>
<meta charset="utf-8">
<title>Rultan Staffing – Retractable Banner</title>
<link rel="stylesheet" href="https://fonts.googleapis.com/css2?family=Montserrat:wght@500;800;900&display=swap">
<style>
  :root {
    --page-bg: #ecebef;
    --banner-bg: #fbfbfd;
    --brand-red: #dc2b33;
    --brand-deep-red: #7a0e14;
    --brand-green: #167a3b;
    --brand-navy: #2b2a6e;
    --brand-yellow: #e3bf1b;
    --brand-purple: #3c2469;
    --brand-magenta: #8e2455;
    --ink: #111111;
    --white: #ffffff;
  }
  * { margin: 0; padding: 0; box-sizing: border-box; }
  html, body {
    width: 1200px;
    height: 900px;
    overflow: hidden;
    background: var(--page-bg);
    font-family: "Montserrat", Arial, sans-serif;
  }
  .banner {
    position: absolute;
    left: 415px;
    top: 20px;
    width: 370px;
    height: 860px;
    background: var(--banner-bg);
    overflow: hidden;
    box-shadow: 0 6px 24px rgba(0,0,0,0.12);
  }
  .banner__backdrop {
    position: absolute;
    inset: 0;
    width: 370px;
    height: 520px;
  }
  .banner__photo {
    position: absolute;
    left: 0;
    top: 120px;
    width: 370px;
    height: 380px;
    background:
      linear-gradient(to bottom, rgba(251,251,253,0) 70%, var(--banner-bg) 100%),
      linear-gradient(100deg, rgba(168,38,70,0.55) 0%, rgba(150,60,110,0.35) 45%, rgba(40,50,90,0.55) 100%);
  }
  .brand {
    position: absolute;
    top: 36px;
    left: 0;
    width: 100%;
    display: flex;
    justify-content: center;
    align-items: center;
    gap: 10px;
  }
  .brand__dot {
    width: 14px;
    height: 14px;
    border-radius: 50%;
    background: var(--brand-navy);
  }
  .brand__name {
    font-weight: 800;
    font-size: 32px;
    color: var(--brand-navy);
    letter-spacing: 0.5px;
  }
  .headline {
    position: absolute;
    top: 525px;
    left: 0;
    width: 100%;
    text-align: center;
    font-weight: 900;
    text-transform: uppercase;
    line-height: 1;
  }
  .headline__connecting {
    display: block;
    color: var(--brand-green);
    font-size: 34px;
    letter-spacing: 0.5px;
  }
  .headline__people {
    display: block;
    margin: 6px 13px 0;
    padding: 5px 0 6px;
    background: linear-gradient(90deg, var(--brand-red), var(--brand-deep-red));
    color: var(--white);
    font-size: 36px;
    letter-spacing: 0.5px;
  }
  .headline__rule {
    display: block;
    margin: 4px auto 0;
    width: 260px;
    height: 3px;
    background: linear-gradient(90deg, transparent, #333 50%, transparent);
  }
  .headline__with {
    display: block;
    margin-top: 12px;
    color: var(--ink);
    font-size: 36px;
  }
  .headline__great {
    display: block;
    margin-top: 14px;
    color: var(--brand-navy);
    font-size: 62px;
  }
  .headline__orgs {
    display: block;
    margin-top: 0;
    color: var(--brand-yellow);
    font-size: 36px;
    letter-spacing: -0.3px;
  }
  .footer-wave {
    position: absolute;
    left: 0;
    bottom: 0;
    width: 370px;
    height: 76px;
  }
  .footer-url {
    position: absolute;
    left: 0;
    bottom: 12px;
    width: 100%;
    text-align: center;
    color: var(--white);
    font-weight: 800;
    font-size: 17px;
  }
</style>
</head>
<body>
  <main class="banner">
    <svg class="banner__backdrop" viewBox="0 0 370 520" aria-hidden="true">
      <defs>
        <linearGradient id="diagonalBand" x1="0" y1="1" x2="1" y2="0">
          <stop offset="0" stop-color="#dc2b33"/>
          <stop offset="0.5" stop-color="#8e2455"/>
          <stop offset="1" stop-color="#3c2469"/>
        </linearGradient>
        <linearGradient id="topWash" x1="0" y1="0" x2="1" y2="0">
          <stop offset="0" stop-color="#f7dfe4"/>
          <stop offset="1" stop-color="#f3f3f7"/>
        </linearGradient>
      </defs>
      <rect width="370" height="520" fill="url(#topWash)"/>
      <polygon points="370,30 370,520 0,520 0,520" fill="url(#diagonalBand)"/>
    </svg>

    <div class="banner__photo" role="img" aria-label="Photo of three young job seekers, a diverse group of women and a man, looking at a tablet and phone"></div>

    <header class="brand">
      <span class="brand__dot"></span>
      <span class="brand__name">Rultan Staffing</span>
    </header>

    <h1 class="headline">
      <span class="headline__connecting">Connecting</span>
      <span class="headline__people">Great People</span>
      <span class="headline__rule"></span>
      <span class="headline__with">With</span>
      <span class="headline__great">Great</span>
      <span class="headline__orgs">Organizations</span>
    </h1>

    <svg class="footer-wave" viewBox="0 0 370 76" preserveAspectRatio="none" aria-hidden="true">
      <defs>
        <linearGradient id="waveFill" x1="0" y1="0" x2="1" y2="0">
          <stop offset="0" stop-color="#dc2b33"/>
          <stop offset="0.5" stop-color="#8e2455"/>
          <stop offset="1" stop-color="#3c2469"/>
        </linearGradient>
      </defs>
      <path d="M0,30 C80,30 130,2 185,2 C245,2 290,34 370,34 L370,76 L0,76 Z" fill="url(#waveFill)"/>
      <path d="M0,30 C80,30 130,2 185,2 C245,2 290,34 370,34 L370,38 C290,38 245,12 185,12 C130,12 80,38 0,38 Z" fill="#fbfbfd"/>
    </svg>
    <p class="footer-url">www.RultanStaffing.example</p>
  </main>
</body>
</html>
```